Custom Cabinet Shop Needs a website design

Hi,
We need a website for a Custom Cabinet Shop and Cabinet parts manufacturing business.
The business has two sides to it. One side provides custom Kitchens, vanities, entertainment units, offices and what not to homeowners and contractors.
The 2nd side of the business provides built to order cabinet boxes and other parts required to put together a project to other cabinet shops, small contractors looking to install there own cabinets.
Website will need a Gallery to display work.
Color scheme to go well with logo.
current website is www.brambleoakcustomcabinets.com
being changed to www.brambleoak.ca
Logo Included in attached files.
Tagline "Joinery with Spirit"
Mission Statement "Our passion is to deliver inspired cabinetry solutions to suit all your needs, supported by our phenomenal star class customer service"
The website should convey quality and professionalism.
Thank you.
Homeowners/ Contractors
Entertainment

```html
<!DOCTYPE html>
<html lang="en">
<head>
<meta charset="utf-8">
<title>Brambleoak Custom Cabinets</title>
<link rel="stylesheet" href="https://fonts.googleapis.com/css2?family=Roboto:wght@400;500;700&family=Roboto+Condensed:wght@400;700&display=swap">
<style>
  :root {
    --accent: #e8431c;
    --ink: #111111;
    --text: #6a6a6a;
    --rule: #e6e6e6;
    --white: #ffffff;
    --footer: #050505;
    --footer-text: #cfcfcf;
  }
  * { box-sizing: border-box; margin: 0; padding: 0; }
  html, body { width: 687px; height: 1200px; overflow: hidden; background: var(--white); }
  body { font-family: "Roboto", Arial, sans-serif; color: var(--text); position: relative; }
  .abs { position: absolute; }

  /* header */
  .brand { left: 59px; top: 30px; display: flex; align-items: center; gap: 8px; }
  .brand-mark { width: 22px; height: 22px; background: var(--accent); border-radius: 50%; }
  .brand-name { font-family: "Roboto Condensed", Arial, sans-serif; font-weight: 700; font-size: 20px; color: var(--ink); letter-spacing: 0.5px; }
  .main-nav { right: 59px; top: 32px; display: flex; align-items: center; gap: 0; }
  .main-nav a { font-family: "Roboto Condensed", Arial, sans-serif; font-size: 7.5px; font-weight: 700; color: var(--ink); text-decoration: none; padding: 0 11px; height: 20px; line-height: 20px; }
  .main-nav a.current { color: var(--accent); border: 1px solid var(--accent); line-height: 18px; margin-right: 3px; }

  /* hero */
  .hero { left: 0; top: 82px; width: 687px; height: 404px;
    background: radial-gradient(ellipse at 45% 45%, #7a5a3e 0%, #4a3526 35%, #2a2420 65%, #1c1f26 100%); }
  .hero-caption { left: 260px; top: 270px; width: 166px; height: 50px; background: rgba(30,30,30,0.72);
    color: var(--white); font-family: "Roboto Condensed", Arial, sans-serif; font-size: 13px; text-align: center; line-height: 50px; text-transform: uppercase; }
  .hero-dots { left: 322px; top: 451px; }

  /* sections */
  .section-title { left: 0; width: 687px; text-align: center; font-family: "Roboto Condensed", Arial, sans-serif; font-weight: 700; font-size: 9px; color: var(--accent); text-transform: uppercase; }
  .title-rule { left: 327px; width: 33px; height: 1px; background: var(--accent); }
  .mission { left: 0; top: 540px; width: 687px; text-align: center; font-size: 10.5px; line-height: 17.5px; color: var(--text); }
  .divider { left: 58px; width: 570px; height: 1px; background: var(--rule); }

  .service { width: 170px; text-align: center; }
  .service-icon { width: 46px; height: 46px; border: 1px solid var(--rule); border-radius: 50%; margin: 0 auto; display: flex; align-items: center; justify-content: center; }
  .service-name { margin-top: 16px; font-family: "Roboto Condensed", Arial, sans-serif; font-weight: 700; font-size: 8.5px; color: var(--ink); }
  .service-text { margin-top: 5px; font-size: 7.3px; line-height: 14.3px; color: var(--text); height: 43px; overflow: hidden; }
  .read-more { display: inline-block; margin-top: 5px; font-size: 7.3px; color: var(--accent); }
  .column-rule { left: 343px; top: 670px; width: 1px; height: 134px; background: var(--rule); }

  .work-strip { left: 60px; top: 939px; width: 569px; height: 137px; display: flex; box-shadow: 0 9px 8px -4px rgba(0,0,0,0.45); }
  .work-tile { flex: 1; height: 100%; }
  .tile-bath { background: linear-gradient(160deg, #c9b9a4 0%, #6d5a4c 55%, #2b211c 100%); }
  .tile-bedroom { background: linear-gradient(160deg, #e6ddd0 0%, #9c8e80 55%, #2f2925 100%); }
  .tile-shelves { background: linear-gradient(160deg, #4c5c6a 0%, #b3b9bb 50%, #727a7c 100%); }
  .tile-bar { background: linear-gradient(160deg, #2a1f1a 0%, #6a4a36 50%, #1b1411 100%); }

  /* footer */
  .site-footer { left: 0; top: 1108px; width: 687px; height: 92px; background: var(--footer); }
  .footer-label { left: 60px; top: 23px; font-size: 6.5px; color: var(--footer-text); text-transform: uppercase; }
  .social { left: 60px; top: 40px; display: flex; gap: 4px; }
  .social span { width: 20px; height: 20px; border-radius: 50%; background: #2b2b2b; }
  .social span.first { background: var(--accent); }
  .footer-nav { right: 58px; top: 25px; font-size: 7px; color: var(--footer-text); }
  .footer-nav span { padding: 0 4px; }
  .copyright { right: 58px; top: 44px; font-size: 7px; color: var(--footer-text); }
</style>
</head>
<body>

<header>
  <div class="abs brand"><span class="brand-mark"></span><span class="brand-name">BRAMBLEOAK</span></div>
  <nav class="abs main-nav">
    <a class="current" href="#">HOME</a>
    <a href="#">GALLERY</a>
    <a href="#">SERVICES</a>
    <a href="#">WARRANTY</a>
    <a href="#">CONTACT</a>
  </nav>
</header>

<div class="abs hero" role="img" aria-label="Basement bar with stone-clad island, live-edge counter, bar stools and dark cabinetry"></div>
<div class="abs hero-caption">Joinery with Spirit</div>
<svg class="abs hero-dots" width="44" height="10" viewBox="0 0 44 10" aria-hidden="true">
  <circle cx="5" cy="5" r="4" fill="#fff"/>
  <circle cx="16" cy="5" r="3.5" fill="none" stroke="#fff" stroke-width="1"/>
  <circle cx="27" cy="5" r="4" fill="#fff"/>
  <circle cx="38" cy="5" r="4" fill="#fff"/>
</svg>

<h2 class="abs section-title" style="top:509px">Welcome to our site</h2>
<div class="abs title-rule" style="top:526px"></div>
<p class="abs mission">Our passion is to deliver inspired cabinetry solutions to suit all your needs,<br>supported by our phenomenal star class customer service</p>

<div class="abs divider" style="top:598px"></div>

<h2 class="abs section-title" style="top:627px">Our services</h2>
<div class="abs title-rule" style="top:644px"></div>

<div class="abs service" style="left:102px;top:670px">
  <div class="service-icon">
    <svg width="13" height="12" viewBox="0 0 13 12" aria-hidden="true"><path d="M6.5 0 L13 6 H11 V12 H8 V8 H5 V12 H2 V6 H0 Z" fill="#111"/></svg>
  </div>
  <div class="service-name">RESIDENTIAL</div>
  <p class="service-text">Here at Brambleoak Custom Cabinets we are proud to be involved in the custom cabinet market.</p>
  <span class="read-more">Read More &#9656;</span>
</div>

<div class="abs column-rule"></div>

<div class="abs service" style="left:409px;top:670px">
  <div class="service-icon">
    <svg width="13" height="12" viewBox="0 0 13 12" aria-hidden="true"><rect x="0" y="3" width="13" height="9" rx="1.5" fill="#111"/><rect x="4" y="0.5" width="5" height="3" rx="1" fill="none" stroke="#111" stroke-width="1.2"/></svg>
  </div>
  <div class="service-name">BUSINESS</div>
  <p class="service-text">At Brambleoak Custom Cabinets we understand that contractors, renovators, home builders, design firms and</p>
  <span class="read-more">Read More &#9656;</span>
</div>

<div class="abs divider" style="top:846px"></div>

<h2 class="abs section-title" style="top:873px">Our work</h2>
<div class="abs title-rule" style="top:890px"></div>
<svg class="abs" style="left:330px;top:907px" width="28" height="14" viewBox="0 0 28 14" aria-hidden="true">
  <circle cx="7" cy="7" r="6.5" fill="#9a9a9a"/><path d="M8.5 4 L5.5 7 L8.5 10" fill="none" stroke="#fff" stroke-width="1.6"/>
  <circle cx="21" cy="7" r="6.5" fill="#9a9a9a"/><path d="M19.5 4 L22.5 7 L19.5 10" fill="none" stroke="#fff" stroke-width="1.6"/>
</svg>

<div class="abs work-strip">
  <div class="work-tile tile-bath" role="img" aria-label="Bathroom vanity with soaker tub and red towels"></div>
  <div class="work-tile tile-bedroom" role="img" aria-label="Bedroom with built-in cabinets around a fireplace"></div>
  <div class="work-tile tile-shelves" role="img" aria-label="Painted built-in shelving wall with lower cabinets"></div>
  <div class="work-tile tile-bar" role="img" aria-label="Dark wood wet bar with wine rack and granite top"></div>
</div>

<footer class="abs site-footer">
  <div class="abs footer-label">Stay with us</div>
  <div class="abs social"><span class="first"></span><span></span><span></span></div>
  <nav class="abs footer-nav"><span>Home</span>|<span>Gallery</span>|<span>Services</span>|<span>Warranty</span>|<span style="padding-right:0">Contact</span></nav>
  <div class="abs copyright">© 2023 by Nora Kell. Proudly created with Plainweb.io</div>
</footer>

</body>
</html>
```